Our new beauty salon requires a price list brochure

Our beauty clinic is a medical grade skin care clinic. So our salon is very clinical and professional in appearance. I would like the colours to be similar to our logo design with some nice texture or abstract shapes thrown in.
Pricelist, contact details and logo is attached
I would prefer it to be a 3 fold brochure.

Target Market(s)

Females aged 30-50

Colors
85acd3
cedeed
c4c4c4
5c5c5c
000000
ffffff
eea3c7
f9d9e8
dbdbdb

Requirements
Must have
• easy to read

```html
<!DOCTYPE html>
<html lang="en">
<head>
<meta charset="utf-8">
<title>Willow Aesthetics – Price List Brochure</title>
<link href="https://fonts.googleapis.com/css2?family=Josefin+Sans:wght@300&family=Open+Sans:wght@400;600&display=swap" rel="stylesheet">
<style>
  :root {
    --page-bg: #ededed;
    --slate: #3f4650;
    --rose-gold: #d9a48c;
    --blush: #f6dcd6;
    --skin-tone: #d9a994;
    --panel-grey: #dcdcdc;
    --rule-pink: #e7c4bb;
    --text-grey: #5c5c5c;
    --white: #ffffff;
  }
  * { margin: 0; padding: 0; box-sizing: border-box; }
  html, body {
    width: 1200px;
    height: 960px;
    overflow: hidden;
    background: var(--page-bg);
  }
  .brochure {
    position: absolute;
    left: 200px;
    top: 50px;
    width: 800px;
    height: 860px;
    display: flex;
    box-shadow: 0 18px 40px rgba(0, 0, 0, 0.12);
  }
  .panel {
    position: relative;
    width: 400px;
    height: 860px;
    overflow: hidden;
  }

  /* Back panel */
  .back-panel { background: var(--panel-grey); }
  .price-list {
    position: absolute;
    left: 40px;
    top: 60px;
    width: 320px;
  }
  .price-group {
    padding: 22px 0 26px;
    border-bottom: 1px solid var(--rule-pink);
  }
  .price-group:last-child { border-bottom: none; }
  .price-heading {
    font-family: "Josefin Sans", sans-serif;
    font-weight: 300;
    font-size: 20px;
    letter-spacing: 3px;
    text-transform: uppercase;
    color: var(--slate);
    margin-bottom: 16px;
  }
  .price-row {
    display: flex;
    justify-content: space-between;
    font-family: "Open Sans", sans-serif;
    font-weight: 400;
    font-size: 15px;
    line-height: 30px;
    color: var(--text-grey);
  }
  .price-row .price {
    width: 64px;
    padding-left: 14px;
    border-left: 1px solid var(--rule-pink);
    color: var(--slate);
    font-weight: 600;
  }
  .back-panel .web-band {
    position: absolute;
    left: 0;
    bottom: 60px;
    width: 100%;
    height: 96px;
    background: var(--slate);
    border-top: 3px solid var(--rose-gold);
    display: flex;
    align-items: center;
    justify-content: center;
  }
  .web-address {
    font-family: "Open Sans", sans-serif;
    font-weight: 600;
    font-size: 24px;
    color: var(--white);
    letter-spacing: 0.5px;
  }
  .back-panel .foot-rule {
    position: absolute;
    left: 0;
    bottom: 36px;
    width: 100%;
    height: 3px;
    background: var(--rule-pink);
  }

  /* Cover panel */
  .cover-panel { background: var(--blush); }
  .cover-photo {
    position: absolute;
    inset: 0;
    background:
      radial-gradient(ellipse 70% 45% at 35% 35%, var(--skin-tone) 0%, rgba(217,169,148,0) 70%),
      linear-gradient(160deg, #c8a48c 0%, #e4c3b4 45%, var(--blush) 100%);
  }
  .cover-curve {
    position: absolute;
    top: 0;
    right: 0;
    width: 160px;
    height: 620px;
  }
  .name-band {
    position: absolute;
    left: 0;
    top: 620px;
    width: 100%;
    height: 130px;
    padding: 0 40px;
    background: rgba(63, 70, 80, 0.92);
    border-top: 4px solid var(--rose-gold);
    border-bottom: 4px solid var(--rose-gold);
    display: flex;
    align-items: center;
    justify-content: center;
  }
  .brand-name {
    font-family: "Josefin Sans", sans-serif;
    font-weight: 300;
    font-size: 21px;
    letter-spacing: 6px;
    white-space: nowrap;
    color: var(--rose-gold);
    text-transform: uppercase;
  }
  .cover-foot-rule {
    position: absolute;
    left: 0;
    top: 800px;
    width: 100%;
    height: 4px;
    background: var(--rose-gold);
  }
</style>
</head>
<body>
  <main class="brochure">
    <section class="panel back-panel">
      <div class="price-list">
        <div class="price-group">
          <h2 class="price-heading">Skin Peels</h2>
          <div class="price-row"><span>Light Peel</span><span class="price">$95</span></div>
          <div class="price-row"><span>Medium Peel</span><span class="price">$150</span></div>
          <div class="price-row"><span>Deep Peel</span><span class="price">$220</span></div>
        </div>
        <div class="price-group">
          <h2 class="price-heading">Facials</h2>
          <div class="price-row"><span>Hydrating Facial</span><span class="price">$120</span></div>
          <div class="price-row"><span>Clinical Facial</span><span class="price">$160</span></div>
          <div class="price-row"><span>LED Therapy</span><span class="price">$80</span></div>
        </div>
        <div class="price-group">
          <h2 class="price-heading">Injectables</h2>
          <div class="price-row"><span>Anti-Wrinkle</span><span class="price">$250</span></div>
          <div class="price-row"><span>Lip Filler</span><span class="price">$450</span></div>
          <div class="price-row"><span>Cheek Filler</span><span class="price">$550</span></div>
        </div>
      </div>
      <div class="web-band">
        <span class="web-address">willowaesthetics.com.au</span>
      </div>
      <div class="foot-rule"></div>
    </section>

    <section class="panel cover-panel">
      <div class="cover-photo" role="img" aria-label="Portrait photograph of a woman with blonde hair resting her hand on her cheek, soft blush tones"></div>
      <svg class="cover-curve" viewBox="0 0 160 620" aria-hidden="true">
        <path d="M60 0 C150 160 150 440 60 620 L160 620 L160 0 Z" fill="#f9e4df" opacity="0.85"/>
      </svg>
      <div class="name-band">
        <span class="brand-name">Willow Aesthetics</span>
      </div>
      <div class="cover-foot-rule"></div>
    </section>
  </main>
</body>
</html>
```